Web and Logo Design for eCommerce site

We're launching a sister brand and require a full design for the site.

The site must have an established feel and appeal to corporate and institutional buyers.
Updates

Just a note about the wireframe design:

The Search & Rescue / Coast Guard / NVDK, etc. in the header area aren't buttons or menu items, but rather just info (along the lines of a tagline).  Sort of a "who we serve" sort of thing.

Worth noting is that it's specifically geared towards LARGE BUYERS.  For example, a police force buying 200 headlamps and 85 pairs of gloves.  So they'll register + sign in and then add a bunch of items to a RFQ.

Aim for a professional, masculine design.

Target Market(s)

We will be selling outdoor gear to the military, law enforcement, fire and rescue and first responders.

Requirements
Must have
• We require:
- Logo (vector based)

Site:
- template page
* main site template, re-skinned version of our current site
* horizontal drop-down menu
- product listings page
* thumbnail view of products
- product details page
* including elements such as product image, color/size selector, descriptions and specs (again, based loosely on our current website)
- account management page
* illustrating basic data entry styles for text box, buttons, grid, etc.

The site needs to be given a responsive design, so 2 versions of each design should be presented for desktop + mobile views.

Additional funds are available if the designer is able to fully implement the designs into a responsive framework such as bootstrap.

Nice to have
• Clean, professional design similar to:

http://military.trailvexagear.com/gov/accessories/gloves.html

http://leaf.ombrivo.com/ProductFind.aspx?language=EN&category=Hardshell&subcat=Waterproof_Jackets

```html
<!DOCTYPE html>
<html lang="en">
<head>
<meta charset="utf-8">
<title>KestrelOps – Army Parka with Liner Olive</title>
<link href="https://fonts.googleapis.com/css2?family=Open+Sans:wght@400;600;700&display=swap" rel="stylesheet">
<style>
:root{
  --topbar:#1d2229;
  --page-bg:#dde6e6;
  --nav-bg:#2b3037;
  --olive:#a3a85a;
  --olive-dark:#4e5a35;
  --price-green:#4b5a2b;
  --price-red:#c4161c;
  --rfq-blue:#1f3f8c;
  --ink:#222;
  --muted:#444;
  --tab-olive:#6b7340;
  --footer-bg:#150f0a;
  --footer-text:#d8d8d8;
  --field:#e6e6e6;
  --rule:#d6d6d6;
}
*{box-sizing:border-box;margin:0;padding:0}
html,body{width:1033px;height:1200px;overflow:hidden}
body{font-family:"Open Sans",Arial,sans-serif;color:var(--ink);background:var(--page-bg)}
.stage{width:1200px;height:1394px;transform:scale(0.86083);transform-origin:0 0;position:relative;background:var(--page-bg)}
.abs{position:absolute}

/* top bar */
.topbar{left:0;top:0;width:1200px;height:34px;background:var(--topbar);color:#ddd;font-size:11px}
.serve{position:absolute;left:110px;top:10px;display:flex;gap:0}
.serve span{padding:0 13px}
.serve span:first-child{padding-left:0}
.serve i{font-style:normal;color:#999}
.social{position:absolute;right:110px;top:6px;display:flex;gap:7px}
.social span{width:21px;height:21px;border-radius:50%;background:#fff;display:block}

/* header */
.header{left:0;top:34px;width:1200px;height:84px;background:#fff}
.brand{position:absolute;left:112px;top:12px;display:flex;align-items:center;gap:10px;color:var(--olive-dark)}
.brand-mark{width:56px;height:56px;background:var(--olive-dark);display:block}
.brand-name{font-weight:700;font-size:34px;line-height:1;letter-spacing:1px}
.brand-sub{font-weight:700;font-size:10.5px;letter-spacing:1.2px;margin-top:4px}
.header-tools{position:absolute;right:110px;top:33px;font-size:13px;color:#666;display:flex;align-items:center;gap:8px}

/* nav */
.mainnav{left:110px;top:118px;width:980px;height:42px;background:var(--nav-bg);display:flex;align-items:center;padding-left:21px;font-size:14px}
.mainnav a{color:var(--olive);text-decoration:none;margin-right:29px}
.mainnav a.active{color:#fff}
.search-btn{position:absolute;right:14px;top:7px;width:26px;height:26px;background:var(--olive)}

/* content */
.content{left:110px;top:169px;width:980px;height:855px;background:#fff}
.crumbs{position:absolute;left:18px;top:22px;font-size:13px}
.crumbs a{color:var(--ink)}
.photo-frame{position:absolute;left:16px;top:62px;width:438px;height:422px;border:1px solid #e1e1e1}
.photo{position:absolute;left:20px;top:10px;width:398px;height:400px;background:radial-gradient(ellipse at center,#b0946b 0%,#9d7f58 55%,#fff 72%)}
.thumbs{position:absolute;left:84px;top:500px;display:flex;align-items:center;gap:8px}
.thumb{width:66px;height:64px;border:1px solid #ddd;background:radial-gradient(circle,#a88a62 45%,#fff 70%)}
.arrow{width:0;height:0;border-top:7px solid transparent;border-bottom:7px solid transparent}
.arrow.l{border-right:9px solid var(--olive-dark);margin-right:26px}
.arrow.r{border-left:9px solid var(--olive-dark);margin-left:18px}

.title{position:absolute;left:489px;top:56px;font-size:26px;font-weight:600}
.desc{position:absolute;left:489px;top:102px;width:450px;font-size:12.5px;line-height:20px;color:var(--muted)}
.more{position:absolute;left:489px;top:191px;font-size:11.5px;color:var(--olive-dark)}
.more a{color:var(--olive-dark)}
.price{position:absolute;top:229px}
.price .label{font-size:15px}
.price .amt{font-size:29px;font-weight:600;line-height:36px}
.retail{left:489px;color:var(--price-green)}
.yours{left:626px;color:var(--price-red);border-left:1px solid var(--rule);padding-left:20px}
.stock{left:805px;top:231px;font-size:11.5px;line-height:20px;border-left:1px solid var(--rule);padding-left:0}
.stock div{padding-left:1px}

.grid{position:absolute;left:489px;top:309px;width:435px;border:1px solid #ccc;border-collapse:collapse;font-size:13px}
.grid th{background:var(--topbar);color:#fff;height:33px;font-size:13px;text-align:center;border-left:1px solid #555}
.grid th:first-child{border-left:none}
.grid td{height:30px;border-left:1px solid #ddd;border-bottom:1px solid #eee;text-align:center}
.grid td:first-child{text-align:left;padding-left:18px;border-left:none}
.box{display:inline-block;width:12px;height:12px;border:1px solid #999;background:#f4f4f4}
.grid-foot{position:absolute;left:489px;top:463px;width:435px;height:30px;background:#dcdcdc;border:1px solid #ccc;border-top:none}
.pager{position:absolute;top:6px;width:20px;height:20px;background:#fff;border:1px solid #bbb}

.qty{position:absolute;left:501px;top:531px;font-size:16px;color:#333}
.qty-field{position:absolute;left:577px;top:524px;width:100px;height:36px;border:1px solid #bbb}
.rfq{position:absolute;left:786px;top:517px;width:139px;height:43px;background:var(--rfq-blue);color:#fff;font-size:18px;font-weight:700;display:flex;align-items:center;justify-content:center;border-radius:2px}

.tabs{position:absolute;left:31px;top:653px;display:flex;gap:13px}
.tab{height:39px;padding:0 27px;font-size:16px;display:flex;align-items:center;background:var(--tab-olive);color:#fff}
.tab.on{background:#fff;color:#333;border:1px solid #ddd;border-bottom:none;height:40px;padding:0 25px}
.panel{position:absolute;left:17px;top:691px;width:942px;height:132px;background:#f2f2f2;border:1px solid #ddd;padding:24px 12px 0 22px;font-size:12.5px;line-height:18px;color:#555}

/* footer */
.footer{left:0;top:1050px;width:1200px;height:344px;background:var(--footer-bg);color:var(--footer-text)}
.fcol{position:absolute;top:38px}
.fcol h3{font-size:16px;font-weight:600;color:#fff;margin-bottom:26px}
.fcol ul{list-style:none;font-size:13px;line-height:22px}
.offer p{font-size:12.5px;line-height:20px;width:260px}
.sub{display:flex;margin-top:20px}
.sub .in{width:191px;height:38px;background:#fff;color:#999;font-size:13px;padding:10px}
.sub .go{width:61px;height:38px;background:#ddd;color:#333;font-size:15px;display:flex;align-items:center;justify-content:center}
.qc .f{width:221px;height:25px;background:var(--field);color:#333;font-size:11.5px;padding:5px 12px;margin-bottom:7px}
.qc .f.msg{height:67px}
.qc .btn{width:86px;height:23px;background:var(--olive);color:#fff;font-size:12px;display:flex;align-items:center;justify-content:center;margin-left:-1px;margin-top:4px}
.copy{position:absolute;left:0;width:1230px;top:294px;text-align:center;font-size:13px;color:#fff}
</style>
</head>
<body>
<div class="stage">

  <div class="abs topbar">
    <div class="serve">
      <span>SEARCH &amp;RECUE</span><i>|</i><span>COAST GUARD</span><i>|</i><span>NVDK</span><i>|</i><span>FIRE</span><i>|</i><span>MILIATRY</span><i>|</i><span>LAW ENFORCEMENT</span>
    </div>
    <div class="social"><span></span><span></span><span></span><span></span></div>
  </div>

  <header class="abs header">
    <div class="brand">
      <span class="brand-mark"></span>
      <div>
        <div class="brand-name">KestrelOps</div>
        <div class="brand-sub">NORTHERN FIELD PRO SUPPLY</div>
      </div>
    </div>
    <div class="header-tools">
      <svg width="18" height="18" viewBox="0 0 24 24"><path fill="#888" d="M6.6 10.8a15 15 0 006.6 6.6l2.2-2.2c.3-.3.7-.4 1-.2 1.1.4 2.3.6 3.6.6.6 0 1 .4 1 1V20c0 .6-.4 1-1 1A17 17 0 013 4c0-.6.4-1 1-1h3.5c.6 0 1 .4 1 1 0 1.3.2 2.5.6 3.6.1.3 0 .7-.2 1z"/></svg>
      <span>Call (+) 0800.555.019</span>
      <svg width="20" height="16" viewBox="0 0 20 16" style="margin-left:6px"><path fill="none" stroke="#888" stroke-width="1.6" d="M1 5h18l-2 10H3zM6 5l3-4M14 5l-3-4M7 8v5M10 8v5M13 8v5"/></svg>
      <span>(0 item) - $0.00</span>
      <span style="font-size:10px">▼</span>
    </div>
  </header>

  <nav class="abs mainnav">
    <a class="active">RESCUE GEAR</a><a>FOOTWEAR</a><a>CLOTHING</a><a>TENTS MATS SLEEPING BAGS</a><a>CAMPING GEAR</a><a>SNOW SPORTS</a><a>BRAND’S</a>
    <div class="search-btn"><svg width="26" height="26" viewBox="0 0 26 26"><circle cx="12" cy="11.5" r="5" fill="none" stroke="#fff" stroke-width="2"/><path d="M15.5 15l4 4" stroke="#fff" stroke-width="2.4"/></svg></div>
  </nav>

  <main class="abs content">
    <div class="crumbs"><a>Rescue Gear</a> &nbsp;&gt;&nbsp; <a>Helmet</a> &nbsp;&gt;&nbsp; <a>Maze Helmet </a></div>

    <div class="photo-frame"><div class="photo" role="img" aria-label="Photo of a khaki long-sleeve field shirt with chest pockets"></div></div>
    <div class="thumbs">
      <span class="arrow l"></span>
      <div class="thumb" role="img" aria-label="Shirt thumbnail, front view"></div>
      <div class="thumb" role="img" aria-label="Shirt thumbnail, detail view"></div>
      <div class="thumb" role="img" aria-label="Shirt thumbnail, side view"></div>
      <span class="arrow r"></span>
    </div>

    <h1 class="title">Army Parka with Liner Olive</h1>
    <p class="desc">All the actual measurements given on the site as "armpit to armpit x 2" refer to the measurements of the garment and not the size it will fit.<br>The best way of checking if an item will fit is to measure a similar garment you have which fits well and compare the measurements.</p>
    <div class="more">+ <a>more</a></div>

    <div class="price retail"><div class="label">RETAIL PRICE</div><div class="amt">$199.99</div></div>
    <div class="price yours"><div class="label">YOUR PRICE LEVEL</div><div class="amt">$150.99</div></div>
    <div class="price stock"><div>Free Canada Shipping</div><div>In Stock</div><div>Ship in 24 hours</div></div>

    <table class="grid">
      <tr><th style="width:130px"></th><th>8”</th><th>8.5”</th><th>9”</th><th>9.5”</th><th>10”</th></tr>
      <tr><td>Orange</td><td><span class="box"></span></td><td><span class="box"></span></td><td><span class="box"></span></td><td><span class="box"></span></td><td><span class="box"></span></td></tr>
      <tr><td>Grey</td><td><span class="box"></span></td><td><span class="box"></span></td><td><span class="box"></span></td><td><span class="box"></span></td><td><span class="box"></span></td></tr>
      <tr><td>Yellow</td><td><span class="box"></span></td><td><span class="box"></span></td><td><span class="box"></span></td><td><span class="box"></span></td><td><span class="box"></span></td></tr>
      <tr><td>Red</td><td><span class="box"></span></td><td><span class="box"></span></td><td><span class="box"></span></td><td><span class="box"></span></td><td><span class="box"></span></td></tr>
    </table>
    <div class="grid-foot">
      <div class="pager" style="left:383px"><svg width="18" height="18"><path d="M11 4l-5 5 5 5" fill="none" stroke="#333" stroke-width="2"/></svg></div>
      <div class="pager" style="left:408px"><svg width="18" height="18"><path d="M7 4l5 5-5 5" fill="none" stroke="#333" stroke-width="2"/></svg></div>
    </div>

    <div class="qty">Quantity:</div>
    <div class="qty-field"></div>
    <div class="rfq">ADD TO RFQ</div>

    <div class="tabs">
      <div class="tab on">Overview</div><div class="tab">Specs</div><div class="tab">Extended Specs</div>
    </div>
    <div class="panel">It is a long established fact that a reader will be distracted by the readable content of a page when looking at its layout. The point of using Lorem Ipsum is that it has a more-or-less normal distribution of letters, as opposed to using 'Content here, content here', making it look like readable English. Many desktop publishing packages and web page editors now use Lorem Ipsum as their default model text, and a search for 'lorem ipsum' will uncover many web sites still in their infancy. Various versions have evolved over the years, sometimes by accident, sometimes on purpose (injected humour and the like).</div>
  </main>

  <footer class="abs footer">
    <div class="fcol" style="left:112px"><h3>Navigation</h3>
      <ul><li>Rescue Gear</li><li>Footwear</li><li>Clothing</li><li>Tents Mats</li><li>Sleeping Bags</li><li>Camping Gear</li><li>Snow Sports</li><li>Brands</li></ul></div>
    <div class="fcol" style="left:311px"><h3>Products</h3>
      <ul><li>Rescue Gear</li><li>Footwear</li><li>Clothing</li><li>Tents Mats</li><li>Sleeping Bags</li><li>Camping Gear</li><li>Snow Sports</li><li>Brands</li></ul></div>
    <div class="fcol offer" style="left:496px"><h3>Get informed for our Special offers</h3>
      <p>Get the best and most interesting discount offers via email.</p>
      <div class="sub"><div class="in">you@example.com</div><div class="go">Enter</div></div></div>
    <div class="fcol qc" style="left:867px"><h3>Quick Contact</h3>
      <div class="f" style="margin-top:-8px">Name:</div><div class="f">Email:</div><div class="f">Phone:</div><div class="f msg">Message:</div>
      <div class="btn">SUMBIT</div></div>
    <div class="copy">CopyRight © 2014 KESTRELOPS All Received</div>
  </footer>

</div>
</body>
</html>
```